COMPANY NAME: Bright Harbor Ventures: Task Description: We are a new UK based business with global rea

Target Market

- Personal and professional development – 30-55 age group, corporate leaders, Eastern European and Asian markets
- On-assignment projects – Corporate market – Eastern European and Asian Markets
- Property investment - 35-65 age group, Europe, USA, Australia

What we need

We need logos and brand design for a suite of web platforms (website, twitter and Facebook profile). We would like to have a cohesive and consistent look across all of our online platforms. The design suite must therefore include social media logos, backgrounds and headers. Specifically we are looking for:

a. Facebook header/page design: likely to have a more youthful look

b. Website: Header, background and layout that is responsive to devices, iPhone primarily, then tablet, then PC (we have purchased a website building package from SiteKettle so if you are familiar with one of their themes, it would be great to have a design that fits with a theme you would recommend); Design should be able to accommodate a place to position video in the medium term but an image in the short term.

c. LinkedIn: header/logo; more corporate look

d. Twitter: background/logo

e. Powerpoint template: background and logo - simple and soft background not busy

f. Electronic Newsletter: logo, header and sidebar; simple and soft background not busy

h. Business card: sophisticated and simple

Colors

We have in mind a preference for colors from the purple family, maybe lavender, so as to appeal to all genders and age groups. Though we are happy to go with a recommendation if you think otherwise.

We would like a look that is professional, airy, bright, fresh, futuristic, insightful, friendly.

Ethos of the brand

- experiencing opportunity and being fulfilled in a changing world
- services are facilitated through insights
- support provided through our product, services and tailored approach to coaching/partnerships (which includes private client match-making)
- we are service providers and passionate about quality and modern leadership skills at all stages in life.

The company name is "Bright Harbor Ventures” - our main message is helping people move to the next level - through investments, personal and professional growth.

Some of our messaging

1. International Leadership in a new world.

2. New technology;

3. Informed;

4. Positively Influential

5. Making a difference;

6. Empowered;

7. Risk free investments;

8. Commercial opportunity;

9. Fulfilled living;

10. Carefree and Fun Living;

11. Progression;

12. Open-minded

13. Energy/dynamic

The Business:
The business is to move people very quickly out of situations that hold them back. the situations could be their own personal situations; their career; their jobs; their teams; their ideas; their finances; their financial opportunities. Remove their fears and give them the strategies to take action. The team are international and have 40 years experience between them in this area.

We do want to come across modern and dynamic, customer outcome focussed, building long-term relationships; international.
Updates

Project Deadline Extended
Reason: We have not found the right designs - we are not just looking for a website design but also images and logos. Most images we can see in the designs are stock images - very standard. We need an image which will be the face of the company, like the shop front window. This main image will be used on social media (top image) and also the home page of the website.

Target Market(s)

30-55 years
Eastern Europe; UK; Asia; Africa; Middle East
Personal, Professional, Corporate, and Financial Growth

Industry/Entity Type

Business Service

Contact Information for Business Card

Simple and stylish
the 3 areas of the business on the reverse -

International look - Offices in UK and San Francisco

Company name
web address www.brightharborventure.com
email director@brightharborventure.com
Facebook bright harbor venture
LinkedIn Bright Harbor Venture
Twitter Bright Harbor Venture
Telephone: +44 (0) 768 213 5597

Logo Text

Something that symbolises unlimited growth - probably not text - could use the word INSIGHT in some way

Number of Pages Required

1 page

Colors
e4daeb
f3f1f8
ffffff

Requirements
Must have
• social media symbols and address
• company name
• Melanie Thorpe
• Director
• Telephone +44 (0) 768 213 5597
• Website name www.brightharborventure.co.uk
• Reverse of Card:
• Discreet, Fast, Bright Harbor Consultancy
• Corporate, Professional, Personal & Property Investment
Nice to have
• not too angular; soft lines; not too cluttered (possibly social media on the reverse and just logo, name, number on the front?
Should not have
• too busy

```html
<!DOCTYPE html>
<html lang="en">
<head>
<meta charset="utf-8">
<title>Bright Harbor Venture</title>
<link href="https://fonts.googleapis.com/css2?family=Open+Sans:wght@400;600;700;800&family=Roboto:wght@400;500;700&display=swap" rel="stylesheet">
<style>
:root{
  --lavender:#e4daeb;
  --mist:#f3f1f8;
  --white:#ffffff;
  --ink:#222222;
  --body:#555555;
  --footer:#333333;
  --red:#d9232d;
  --overlay:#5e5566;
  --social:#3b4a8a;
  --line:#dcdcdc;
}
*{margin:0;padding:0;box-sizing:border-box}
html,body{width:1200px;height:2671px;overflow:hidden;background:var(--white)}
body{position:relative;font-family:"Open Sans",Arial,sans-serif;color:var(--ink)}
.abs{position:absolute}

/* header */
.hero{left:0;top:0;width:968px;height:573px;background:linear-gradient(120deg,#c9d2dc 0%,#8e9aa8 35%,#4a5363 70%,#bfc7d1 100%)}
.header{left:110px;top:0;width:880px;height:90px;background:var(--white);border-bottom-left-radius:60px}
.logo{display:flex;align-items:center;gap:12px;white-space:nowrap}
.logo-mark{width:48px;height:48px;border-radius:50%;border:2px solid #777;flex:none}
.logo-name{font-weight:700;font-size:24px;color:#333}
.header .logo{position:absolute;left:22px;top:17px}
.follow-label{left:561px;top:32px;font-size:9px;color:#555;letter-spacing:.3px}
.socials{display:flex;gap:7px}
.socials span{width:21px;height:21px;border-radius:50%;background:var(--social);display:block}
.header .socials{position:absolute;left:647px;top:27px}
.search{left:780px;top:27px;width:90px;height:29px;border:1px solid #bbb;font-size:9px;color:#aaa;display:flex;align-items:center;gap:6px;padding-left:10px}
.burger{left:901px;top:27px;width:34px}
.burger span{display:block;height:2px;background:#888;margin-bottom:11px}

.hero-caption{left:659px;top:320px;width:309px;height:125px;background:rgba(40,40,45,.85);padding:18px 0 0 32px;overflow:hidden}
.hero-caption h1{font-size:30px;font-weight:800;color:var(--white);white-space:nowrap}
.hero-caption p{font-size:12px;color:#eee;line-height:19px;margin-top:6px;white-space:nowrap}
.dots{left:530px;top:461px;display:flex;gap:12px}
.dots span{width:10px;height:10px;background:var(--white);display:block}
.dots span.on{background:transparent;border:2px solid var(--white);width:12px;height:12px;margin-top:-1px}

.nav{left:979px;top:108px;width:203px;list-style:none;background:var(--white)}
.nav li{height:52px;border-bottom:1px solid var(--line);font-size:12px;color:#333;padding:0 0 0 20px;display:flex;align-items:center}
.nav li.active span{background:var(--lavender);padding:7px 10px;margin-left:-10px}

/* service cards */
.services{left:134px;top:516px;width:934px;height:329px;background:var(--white);border-radius:70px;box-shadow:0 6px 24px rgba(0,0,0,.12)}
.service{top:525px;width:292px;height:320px;background:var(--white);border:1px solid #ddd;border-radius:70px;overflow:hidden;text-align:center;box-shadow:0 4px 14px rgba(0,0,0,.1)}
.service .photo{height:169px}
.service h3{font-size:16px;font-weight:600;margin-top:22px}
.service p{font-size:12px;color:var(--body);line-height:20px;margin:10px 30px 0}
.service .more{font-size:10px;font-weight:700;margin-top:16px;display:inline-flex;align-items:center;gap:6px}

/* features */
.features{left:134px;top:872px;width:934px;height:351px;border-radius:80px;overflow:hidden;background:linear-gradient(110deg,#cfcbd8 0%,#dfe3ec 50%,#c8c2cf 100%)}
.features .shade{left:0;top:0;width:380px;height:351px;background:var(--overlay);opacity:.92;clip-path:polygon(0 0,100% 0,88% 100%,0 100%)}
.features h2{left:80px;top:52px;font-size:26px;font-weight:800;color:var(--white);text-decoration:underline;text-underline-offset:5px}
.features h4{left:80px;top:104px;font-size:15px;font-weight:700;color:var(--white);line-height:22px}
.features p{left:80px;top:162px;font-size:12.5px;color:#f0f0f0;line-height:19px;width:260px}
.watch{left:80px;top:249px;width:137px;height:41px;border-radius:21px;background:var(--red);color:var(--white);font-size:13px;font-weight:700;display:flex;align-items:center;justify-content:center}
.play{left:425px;top:107px}

/* welcome */
.welcome{left:134px;top:1242px;width:934px;height:369px;border-radius:80px;overflow:hidden;background:var(--lavender)}
.welcome .photo{left:530px;top:0;width:404px;height:369px}
.welcome h2{left:57px;top:42px;font-size:18px;font-weight:700}
.welcome .copy{left:58px;top:80px;width:430px;font-family:Roboto,Arial,sans-serif;font-size:12.5px;color:#444;line-height:19px}
.welcome .copy p{margin-bottom:12px}

/* headings */
.section-title{left:0;width:1200px;text-align:center;font-size:18px;font-weight:700}
.section-title::after{content:"";display:block;width:118px;height:4px;background:var(--lavender);margin:9px auto 0}

/* assignments */
.assign{top:1703px;width:294px;height:260px;border-radius:70px;overflow:hidden;box-shadow:0 4px 14px rgba(0,0,0,.12)}
.assign .photo{height:260px}
.assign .band{position:absolute;left:0;bottom:0;width:100%;height:62px;background:rgba(228,218,235,.92);text-align:center;padding-top:14px;font-size:16px;font-weight:600}

/* private client */
.private{left:0;top:2001px;width:1200px;height:359px;background:var(--mist)}
.client{top:2118px;width:240px;text-align:center}
.client .icon{width:136px;height:136px;border-radius:50%;background:var(--lavender);margin:0 auto;display:flex;align-items:center;justify-content:center}
.client p{font-family:Roboto,Arial,sans-serif;font-size:15px;line-height:21px;margin-top:26px;color:#222}

/* footer */
.footer{left:0;top:2360px;width:1200px;height:267px;background:var(--footer);color:var(--white)}
.footer .logo{position:absolute;left:132px;top:52px;gap:10px}
.footer .logo-mark{width:42px;height:42px;border-color:var(--white)}
.footer .logo-name{color:var(--white);font-size:20px}
.footer h5{font-size:12px;font-weight:700}
.footer .col{font-family:Roboto,Arial,sans-serif;font-size:11px;line-height:25px;color:#eee;white-space:nowrap}
.email{left:847px;top:82px;width:221px;height:41px;background:var(--white);color:#444;font-size:12px;padding:12px 14px}
.signup{left:847px;top:141px;width:221px;height:48px;background:var(--lavender);color:#333;font-size:18px;font-weight:700;display:flex;align-items:center;justify-content:center}
.copyright{left:0;top:2627px;width:1200px;height:44px;background:var(--lavender);text-align:center;font-size:10px;color:#333;padding-top:15px;font-family:Roboto,Arial,sans-serif}
</style>
</head>
<body>

<div class="abs hero" role="img" aria-label="Photo of two businessmen reviewing work at a laptop in an office"></div>

<header class="abs header">
  <div class="logo"><span class="logo-mark"></span><span class="logo-name">Bright Harbor Venture</span></div>
  <div class="abs follow-label">FOLLOW US ON :</div>
  <div class="socials" aria-label="Social media links"><span></span><span></span><span></span><span></span></div>
  <div class="abs search">
    <svg width="9" height="9" viewBox="0 0 10 10"><circle cx="4" cy="4" r="3" fill="none" stroke="#999" stroke-width="1.4"/><line x1="6.3" y1="6.3" x2="9" y2="9" stroke="#999" stroke-width="1.4"/></svg>SEARCH
  </div>
  <div class="abs burger"><span></span><span></span><span></span></div>
</header>

<div class="abs hero-caption">
  <h1>CONSULTING COMPANY</h1>
  <p>But I must explain to you how all this mistaken idea of<br>denouncing pleasure and praising.</p>
</div>
<div class="abs dots"><span></span><span class="on"></span><span></span><span></span><span></span></div>

<ul class="abs nav">
  <li class="active"><span>Home</span></li>
  <li>About Us</li>
  <li>Our Values</li>
  <li>Testimonials</li>
  <li>Social Media</li>
  <li>News Alert</li>
  <li>Contact Us</li>
</ul>

<div class="abs services"></div>
<article class="abs service" style="left:144px">
  <div class="photo" role="img" aria-label="Portrait photo of a smiling businessman" style="background:linear-gradient(135deg,#e9e9ea,#b7b2ad)"></div>
  <h3>Professional and Personal</h3>
  <p>At vero eos et accusamus et iusto odio dignissimos ducimus.</p>
  <div class="more">READ MORE <svg width="6" height="8" viewBox="0 0 6 8"><path d="M0 0L6 4L0 8Z" fill="#222"/></svg></div>
</article>
<article class="abs service" style="left:454px">
  <div class="photo" role="img" aria-label="Photo of a group of business leaders standing together" style="background:linear-gradient(135deg,#8b95a3,#2e333b)"></div>
  <h3>Next Generation Leaders</h3>
  <p>At vero eos et accusamus et iusto odio dignissimos ducimus.</p>
  <div class="more">READ MORE <svg width="6" height="8" viewBox="0 0 6 8"><path d="M0 0L6 4L0 8Z" fill="#222"/></svg></div>
</article>
<article class="abs service" style="left:761px">
  <div class="photo" role="img" aria-label="Photo of a team in a consultation meeting around a table" style="background:linear-gradient(135deg,#c4c8cd,#6c7078)"></div>
  <h3>Consultation Options</h3>
  <p>At vero eos et accusamus et iusto odio dignissimos ducimus.</p>
  <div class="more">READ MORE <svg width="6" height="8" viewBox="0 0 6 8"><path d="M0 0L6 4L0 8Z" fill="#222"/></svg></div>
</article>

<section class="abs features" role="img" aria-label="Video still of a presenter holding a tablet in front of an audience">
  <div class="abs shade"></div>
  <h2 class="abs">OUR FEATURES</h2>
  <h4 class="abs">BUT I MUST EXPLAIN TO YOU<br>HOW ALL THIS</h4>
  <p class="abs">At vero eos et accusamus et iusto odio dignissimos ducimus qui blanditiis praesentium voluptatum.</p>
  <div class="abs watch">WATCH NOW</div>
  <svg class="abs play" width="100" height="100" viewBox="0 0 100 100"><circle cx="50" cy="50" r="48" fill="var(--red)"/><circle cx="50" cy="50" r="33" fill="none" stroke="#fff" stroke-width="6"/><path d="M42 35L66 50L42 65Z" fill="#fff"/></svg>
</section>

<section class="abs welcome">
  <h2 class="abs">WELCOME TO OUR SITE</h2>
  <div class="abs copy">
    <p>If you seek an experienced and trusted partner to work with you on an assignment or simply want some strategies to move your personal or professional talents to the next level then you are in the right place.</p>
    <p>If you feel that the pace of change in business is so fast that to be an outstanding leader you should ensure you are brought up to speed regularly then you are in the right place.</p>
    <p>If you are hearing about the essential new leadership essentials and you are ready to hear how to adopt them into your life or business then you are at the right place.</p>
    <p>I am so convinced that you will be delighted with how fast you can make change happen.</p>
  </div>
  <div class="abs photo" role="img" aria-label="Photo of a trainer presenting at a whiteboard to a seated group" style="background:linear-gradient(135deg,#d8cbbb,#8f8a86)"></div>
</section>

<h2 class="abs section-title" style="top:1643px">ON ASSIGNMENT</h2>
<article class="abs assign" style="left:134px">
  <div class="photo" role="img" aria-label="Overhead photo of a team working around a table" style="background:linear-gradient(135deg,#9a9a98,#3c3c3c)"></div>
  <div class="band">Team Cohesion Strategy</div>
</article>
<article class="abs assign" style="left:454px">
  <div class="photo" role="img" aria-label="Photo of a businessman in front of a wall of sketched charts" style="background:linear-gradient(135deg,#f1f1f1,#b8b8b8)"></div>
  <div class="band">Go To Market Strategy</div>
</article>
<article class="abs assign" style="left:774px">
  <div class="photo" role="img" aria-label="Photo of a businessman with a glowing world map" style="background:linear-gradient(135deg,#6f8fb8,#1f3556)"></div>
  <div class="band">Internationalisation Strategy</div>
</article>

<section class="abs private">
  <h2 class="abs section-title" style="top:40px">PRIVATE CLIENT</h2>
</section>
<div class="abs client" style="left:88px">
  <div class="icon"><svg width="64" height="54" viewBox="0 0 64 54" fill="none" stroke="#333" stroke-width="3"><path d="M6 18h10l24-12v40L16 34H6z"/><path d="M14 34l5 14h7l-4-14"/><path d="M48 14l8-5M50 25h9M48 36l8 5"/></svg></div>
  <p>Promotion and<br>cash-buyer matching</p>
</div>
<div class="abs client" style="left:341px">
  <div class="icon"><svg width="64" height="64" viewBox="0 0 64 64" fill="#333"><circle cx="36" cy="12" r="9"/><circle cx="24" cy="28" r="8"/><path d="M4 44h14l14 4h14l12-8 3 3-14 13H30l-14-4H4z"/></svg></div>
  <p>Investment:<br>high return projects</p>
</div>
<div class="abs client" style="left:599px">
  <div class="icon"><svg width="60" height="62" viewBox="0 0 60 62" fill="#333"><rect x="4" y="6" width="26" height="56"/><rect x="34" y="18" width="22" height="44"/><g fill="#e4daeb"><rect x="9" y="12" width="6" height="6"/><rect x="19" y="12" width="6" height="6"/><rect x="9" y="24" width="6" height="6"/><rect x="19" y="24" width="6" height="6"/><rect x="9" y="36" width="6" height="6"/><rect x="19" y="36" width="6" height="6"/><rect x="40" y="26" width="10" height="5"/><rect x="40" y="37" width="10" height="5"/><rect x="40" y="48" width="10" height="5"/></g></svg></div>
  <p>Commercial:<br>Hotels and Senior Housing</p>
</div>
<div class="abs client" style="left:877px">
  <div class="icon"><svg width="64" height="64" viewBox="0 0 64 64" fill="none" stroke="#333" stroke-width="3"><circle cx="32" cy="32" r="27"/><ellipse cx="32" cy="32" rx="12" ry="27"/><path d="M5 32h54M9 18h46M9 46h46M32 5v54"/></svg></div>
  <p>Prestige Residential:<br>US, Australia, UK</p>
</div>

<footer class="abs footer">
  <div class="logo"><span class="logo-mark"></span><span class="logo-name">Bright Harbor Venture</span></div>
  <h5 class="abs" style="left:246px;top:132px">FOLLOW US</h5>
  <div class="abs socials" style="left:216px;top:166px"><span></span><span></span><span></span><span></span></div>

  <h5 class="abs" style="left:466px;top:50px">CONTACT US</h5>
  <div class="abs col" style="left:466px;top:78px">418 Larkspur Lane<br>Fairmont, CA 90412.<br>Email: director@brightharborventure.com<br>Call: &nbsp;+44 (0) 768 213 5597</div>

  <h5 class="abs" style="left:710px;top:50px">MENU</h5>
  <div class="abs col" style="left:710px;top:76px">About You<br>About Us<br>Our Values<br>Testimonials<br>Social Media<br>News Alert</div>

  <h5 class="abs" style="left:847px;top:50px">NEWSLETTER SIGNUP!</h5>
  <div class="abs email">E mail id</div>
  <div class="abs signup">SIGNUP!</div>
</footer>
<div class="abs copyright">Copyrights @ 2016 All Rights Reserved</div>

</body>
</html>
```